CORAL TIDE LAUNDROMAT

I NEED A SIGN FOR A NEW LAUNDROMAT THAT I HAVE BUILT
IN THE CITY OF DARWIN BESIDE MY CURRENT HOTEL I OWN
THIS IS A SEMI STAND ALONE BUSNIESS
DARWIN IS A LAID BACK CITY IN AUSTRALIA WERE THING ARE A BIT CHEEKY THE SIGN /LOGO ECT WILL BE APPRO 2 METERS TALL BY 6 METERS LONG ,6 FOOT BY 18 FOOT
sign viewing point is 5 meters to 100 meters

i have put a logo up of my current hotel as a guide it docent have to mach it just food for thought idea

building colour is white and black

like it to be fun or a little sexy risky

```html
<!DOCTYPE html>
<html lang="en">
<head>
<meta charset="utf-8">
<title>Coral Tide Laundromat – Sign</title>
<link rel="stylesheet" href="https://fonts.googleapis.com/css2?family=Jost:wght@700&display=swap">
<style>
  :root {
    --backdrop: #e4e4e4;
    --sky-top: #cfe6f6;
    --sky-mid: #eaf5fc;
    --foam: #ffffff;
    --wave-light: #a9d3f0;
    --wave-deep: #3f8fd0;
    --ink: #222222;
    --brand-blue: #0f57a3;
    --outline: #ffffff;
  }
  * { margin: 0; padding: 0; box-sizing: border-box; }
  html, body {
    width: 1200px;
    height: 599px;
    overflow: hidden;
    background: var(--backdrop);
  }
  .sign {
    position: absolute;
    left: 28px;
    top: 108px;
    width: 1144px;
    height: 382px;
    display: block;
  }
  .sign-title {
    font-family: "Jost", "Futura", sans-serif;
    font-weight: 700;
    paint-order: stroke fill;
    stroke: var(--outline);
    stroke-linejoin: round;
  }
  .title-top { fill: var(--ink); font-size: 128px; stroke-width: 6px; }
  .title-bottom { fill: var(--brand-blue); font-size: 132px; stroke-width: 8px; }
</style>
</head>
<body>
<svg class="sign" viewBox="0 0 1144 382" xmlns="http://www.w3.org/2000/svg">
  <defs>
    <linearGradient id="sky" x1="0" y1="0" x2="0" y2="1">
      <stop offset="0" stop-color="var(--sky-top)"/>
      <stop offset="0.55" stop-color="var(--sky-mid)"/>
      <stop offset="1" stop-color="var(--foam)"/>
    </linearGradient>
    <linearGradient id="washer-area" x1="0" y1="0" x2="1" y2="1">
      <stop offset="0" stop-color="#ffffff"/>
      <stop offset="1" stop-color="#d6ebf9"/>
    </linearGradient>
  </defs>

  <rect class="sign-panel" width="1144" height="382" fill="url(#sky)"/>

  <g class="wave-bands" fill="none" stroke-linecap="round">
    <path d="M0 232 C180 200 320 270 520 236 S860 210 1144 240" stroke="var(--wave-light)" stroke-width="10"/>
    <path d="M0 252 C200 222 340 290 540 256 S880 232 1144 262" stroke="var(--wave-deep)" stroke-width="4"/>
    <path d="M0 300 C220 268 380 330 600 292 S900 276 1144 306" stroke="var(--wave-light)" stroke-width="6"/>
    <path d="M0 340 C240 318 420 364 640 332 S940 320 1144 344" stroke="var(--wave-light)" stroke-width="4" opacity="0.7"/>
  </g>

  <g class="washer-illustration" role="img" aria-label="Illustration of a tilted spinning washing machine with water splash and soap bubbles">
    <rect x="640" y="44" width="330" height="318" rx="24" fill="url(#washer-area)" opacity="0.9"/>
  </g>

  <text class="sign-title title-top" x="20" y="142" textLength="440" lengthAdjust="spacing">CORAL</text>
  <text class="sign-title title-bottom" x="20" y="277" textLength="1098" lengthAdjust="spacingAndGlyphs">TIDE LAUNDROMAT</text>
</svg>
</body>
</html>
```